I have a website called Okenta Holdings (okentaholdings.com) that I would like to have redesigned. Most of the content is already created, but I need a new design. You can also see my other website at brambleacres.com. I am open to a new logo or modifying the current logo if you have a good idea. Please feel free to use other images for the home page (and maybe some other locations) if you feel they provide a better look and feel to the website. I prefer a modern look.

Important: You do not have to use the images I've provided for the home page. Feel free to find your own stock photos. You don't have to pay for them unless I select your design.

1) Please use wix.com to make your changes so that I can edit it later.
2) I will need all the graphics files to be saved so I can dowload it for later.
3) I will be adding more content to the site later.
4) This site will likely be transferred over to brambleacres.com so if you make a logo please make one for Okenta Holdings and one for Bramble Acres.
5) You can use other images that you feel would help the look and feel of the website.

```html
<!DOCTYPE html>
<html lang="en">
<head>
<meta charset="utf-8">
<title>Bramble Acres – Website Pages</title>
<link href="https://fonts.googleapis.com/css2?family=Inter:wght@400;500;600;700&display=swap" rel="stylesheet">
<style>
:root{
  --stage:#000;
  --navy:#0a1b36;
  --navy-2:#10284d;
  --blue:#1b6fd6;
  --sky:#3b92f2;
  --light:#eef1f5;
  --paper:#ffffff;
  --ink:#1b2130;
  --muted:#5d6676;
  --yellow:#f6ea7c;
  --band:#2b313c;
}
*{margin:0;padding:0;box-sizing:border-box}
html,body{width:1200px;height:687px;overflow:hidden;background:var(--stage)}
body{position:relative;font-family:"Inter",sans-serif;color:var(--ink)}
.page{position:absolute;top:15px;width:225px;background:var(--paper);overflow:hidden}
.page *{position:absolute}
.page .flow, .page .flow *{position:static}
.nav{left:0;top:0;width:225px;height:19px;background:var(--paper)}
.brand{display:flex;align-items:center;gap:2px;font-weight:700;font-size:4.6px;line-height:1;color:var(--blue)}
.brand .mark{position:static;width:6px;height:6px;background:var(--blue);border-radius:1px}
.brand.on-dark{color:#fff}
.brand.on-dark .mark{background:var(--sky)}
.nav .brand{left:16px;top:6px}
.nav-links{top:8px;display:flex;gap:7px;font-size:3.2px;font-weight:500}
.nav-links span{position:static}
.nav-links .current{color:var(--sky)}
.btn{display:flex;align-items:center;justify-content:center;background:var(--blue);color:#fff;font-weight:600;border-radius:2px;font-size:3.2px}
.nav .btn{left:181px;top:4px;width:28px;height:11px}
.photo{display:block}
.hero-title{left:0;width:225px;text-align:center;color:#fff;font-weight:500;letter-spacing:-.4px;line-height:.95}
.hero-copy{left:0;width:225px;text-align:center;color:#fff;font-size:2.8px;line-height:1.3;padding:0 50px}
.para{font-size:2.4px;line-height:1.45;color:var(--muted)}
.h-blue{color:var(--blue);font-weight:600}
.footer{left:0;width:225px;height:62px;background:var(--navy);color:#fff}
.footer .brand{left:15px;top:24px}
.f-col{display:flex;flex-direction:column;gap:3.2px;font-size:3px}
.f-col span{position:static}
.f-col .f-head{color:var(--sky);font-weight:600}
.f-input{left:158px;width:51px;height:9px;border-radius:5px;background:var(--navy-2);font-size:2.6px;color:#8090aa;display:flex;align-items:center;justify-content:center}
.f-btn{left:158px;width:51px;height:10px;border-radius:5px;background:var(--sky);font-size:3px;color:#fff;display:flex;align-items:center;justify-content:center}
.copy{left:15px;bottom:4px;font-size:2.4px;color:#6f7f99}
.socials{right:16px;bottom:4px;display:flex;gap:3px}
.socials i{position:static;display:block;width:3.5px;height:3.5px;border:.5px solid #8fa3c2;border-radius:50%}
.partners{left:0;width:225px;height:19px;display:flex;align-items:center;justify-content:center;gap:9px;color:#fff;font-size:4.4px;font-weight:600}
.partners span{position:static}
.partners .lead{font-size:3.4px;font-weight:500;padding-right:6px;border-right:.6px solid #fff}
.card{background:var(--paper);border-radius:4px}
.focus-title{left:0;width:100%;text-align:center;font-size:5.4px;font-weight:600;color:var(--ink)}
.focus-col{background:#e8edf4;border-radius:2px;padding:3px}
.focus-col b{display:block;position:static;color:var(--blue);font-size:3.4px;text-align:center;line-height:1.1;margin-bottom:3px}
.focus-col ul{position:static;list-style:disc;padding-left:4px;font-size:2.1px;line-height:1.35;color:var(--muted)}
.focus-col li{position:static}
.types{background:var(--yellow);border-radius:2px;display:flex;align-items:center;gap:8px;padding:0 16px}
.types b{position:static;font-size:5px;line-height:.9;font-weight:600}
.types ul{position:static;list-style:disc;padding-left:3px;font-size:2.5px;line-height:1.3}
.types li{position:static}
.proj{width:95px;height:85px;background:var(--navy)}
.proj .img{left:0;top:0;width:95px;height:63px}
.proj .tag{left:4px;top:3px;background:rgba(10,27,54,.75);color:#fff;font-size:2.8px;padding:1px 3px}
.proj .name{left:0;top:66px;width:95px;text-align:center;color:#fff;font-size:3.8px;font-weight:600}
.proj .meta{left:6px;top:72px;width:83px;text-align:center;color:#b9c6da;font-size:2.6px;line-height:1.3}
.member{width:62px;height:78px;background:var(--navy)}
.member .img{left:0;top:0;width:62px;height:62px}
.member .name{left:0;top:64px;width:62px;text-align:center;color:#fff;font-size:3.6px;font-weight:600}
.member .role{left:0;top:70px;width:62px;text-align:center;color:#c4d0e2;font-size:2.8px}
.stat{background:var(--paper);border-radius:2px;text-align:center;height:27px;display:flex;flex-direction:column;justify-content:center}
.stat b{position:static;color:var(--blue);font-size:6px;font-weight:500}
.stat span{position:static;font-size:2.4px;color:var(--muted);line-height:1.1}
.field-label{left:15px;font-size:3px;color:var(--ink)}
.field{left:15px;width:77px;background:#eceef2;border-radius:1px}
.info h4{position:static;color:var(--blue);font-size:6px;font-weight:500;margin-bottom:3px}
.info p{position:static;font-size:3px;line-height:1.35;color:var(--muted)}
</style>
</head>
<body>

<!-- HOME -->
<section class="page" style="left:17px;height:657px" aria-label="Home page">
  <header class="nav">
    <div class="brand"><i class="mark"></i>Bramble Acres</div>
    <nav class="nav-links" style="left:82px"><span class="current">Home</span><span>About</span><span>Strategy</span><span>Projects</span></nav>
    <div class="btn">Investor Login</div>
  </header>
  <div class="photo" role="img" aria-label="Aerial night view of a construction site" style="left:0;top:19px;width:225px;height:122px;background:radial-gradient(ellipse at 50% 40%,#3d3a48,#1d2030 60%,#15161f)"></div>
  <h1 class="hero-title" style="top:51px;font-size:15px">Building Together<br><span style="position:static;color:var(--sky)">Growing Together</span></h1>
  <p class="hero-copy" style="top:84px;font-size:5px;line-height:1.1">Private Commercial Real Estate Investment And Development Firm</p>
  <div class="btn" style="left:96px;top:103px;width:33px;height:10px">Get Started</div>
  <div class="partners" style="top:141px;background:var(--band)"><span class="lead">Corporate Partners</span><span>Tavrin</span><span>Corveth</span><span>Lumo</span><span>Halden</span><span>Ashby &amp; Co</span></div>
  <div style="left:0;top:160px;width:225px;height:224px;background:var(--light)"></div>
  <div class="card" style="left:16px;top:170px;width:210px;height:83px;width:194px">
    <h2 class="h-blue" style="left:9px;top:9px;font-size:7px;line-height:.95">About<br><span style="position:static">Bramble Acres</span></h2>
    <p class="para" style="left:9px;top:28px;width:97px">Bramble Acres is a private real estate firm that focuses on the purchase, growth, oversight and sale of many kinds of commercial property, including multifamily, single-family, hospitality, self-storage and flex space. The firm carries out its plan through long-standing ties that help it acquire and develop assets in select target markets. It is now centered on buying and building in the southern part of the country.</p>
    <div class="btn" style="left:9px;top:68px;width:28px;height:9px">Learn More</div>
    <div class="photo" role="img" aria-label="Three partners standing outdoors in suits" style="left:110px;top:6px;width:74px;height:70px;background:linear-gradient(160deg,#8aa2b8,#3b4a5e 70%,#2a3544)"></div>
  </div>
  <h2 style="left:16px;top:268px;font-size:7px;font-weight:500">Our Projects</h2>
  <div style="left:182px;top:265px;width:28px;height:10px;border:.6px solid var(--blue);border-radius:5px;color:var(--blue);font-size:3px;display:flex;align-items:center;justify-content:center">View All ›</div>
  <div class="photo" role="img" aria-label="Rendering of a tan apartment complex" style="left:16px;top:280px;width:114px;height:77px;background:linear-gradient(180deg,#9db9d6,#c9b58e 55%,#6c7f52)"></div>
  <div class="photo" role="img" aria-label="Modern apartment buildings" style="left:134px;top:280px;width:36px;height:37px;background:linear-gradient(180deg,#a9b9c8,#5e6770)"></div>
  <div class="photo" role="img" aria-label="White industrial building" style="left:173px;top:280px;width:36px;height:37px;background:linear-gradient(180deg,#2f63b8,#d4d8de)"></div>
  <div style="left:134px;top:320px;width:36px;height:37px;background:#2356b2"><span style="left:3px;bottom:3px;color:#fff;font-size:3.8px;font-weight:600;line-height:1">Stonebay<br>Harbor<br>Residences</span></div>
  <div class="photo" role="img" aria-label="Apartment entrance sign with landscaping" style="left:173px;top:320px;width:36px;height:37px;background:linear-gradient(180deg,#4e6a88,#3e5a3a)"></div>
  <div class="photo" role="img" aria-label="Dark lobby interior" style="left:0;top:369px;width:225px;height:130px;background:linear-gradient(120deg,#1d2f52,#33425e 50%,#1a2238)"></div>
  <h2 style="left:15px;top:410px;color:#fff;font-size:11px;font-weight:500;line-height:.95">Strategies of<br><span style="position:static;color:var(--sky)">Bramble<br>Acres</span></h2>
  <div class="btn" style="left:16px;top:460px;width:36px;height:10px">Our Strategies</div>
  <div class="card" style="left:98px;top:390px;width:111px;height:82px;border-radius:2px">
    <h3 class="focus-title" style="top:4px">Investment Focus</h3>
    <div class="focus-col" style="left:5px;top:14px;width:50px;height:66px"><b>Acquisitions: Distressed/Value-Add</b><ul><li>Value-Add Deals that offer a strong mix of yield and upside.</li><li>Distressed Assets with upside potential.</li><li>Major Metro Areas</li><li>Asset Value $10 - $75mm</li></ul></div>
    <div class="focus-col" style="left:59px;top:14px;width:48px;height:66px"><b>Development</b><ul><li>Site Selection</li><li>Undeveloped Land</li><li>Zoning and Entitlements</li><li>Urban Redevelopment</li><li>Multiple Build Types:</li><li>Single Story Garden</li><li>Wrap Construction</li><li>Podium Construction</li><li>Tiltwall</li></ul></div>
  </div>
  <div class="types" style="left:105px;top:461px;width:95px;height:21px"><b>Product<br>Types</b><ul><li>Multifamily</li><li>Industrial</li><li>SFR Communities</li></ul><ul><li>Self-Storage</li><li>Hospitality</li><li>Retail</li></ul></div>
  <div style="left:0;top:499px;width:225px;height:96px;background:var(--light)"></div>
  <h2 class="h-blue" style="left:0;top:516px;width:225px;text-align:center;font-size:7px;font-weight:500">Our Testimonials</h2>
  <div class="card" style="left:49px;top:530px;width:127px;height:40px;border-radius:2px">
    <p style="left:10px;top:7px;width:107px;text-align:center;font-size:3px;line-height:1.35;color:var(--muted)">Their team was clear and steady from start to finish. Every step was well planned, and the results came in ahead of what we had hoped for.</p>
    <p style="left:0;top:28px;width:127px;text-align:center;font-size:3px;font-weight:600">Nora Vance</p>
    <p style="left:0;top:33px;width:127px;text-align:center;font-size:2.8px;color:var(--muted)">CEO at Keel Agency</p>
  </div>
  <svg style="left:33px;top:546px" width="6" height="6" viewBox="0 0 6 6"><path d="M5 3H1M3 1L1 3l2 2" stroke="#1b6fd6" stroke-width=".7" fill="none"/></svg>
  <svg style="left:186px;top:546px" width="6" height="6" viewBox="0 0 6 6"><path d="M1 3h4M3 1l2 2-2 2" stroke="#1b6fd6" stroke-width=".7" fill="none"/></svg>
  <svg style="left:106px;top:577px" width="14" height="3" viewBox="0 0 14 3"><circle cx="1.5" cy="1.5" r="1.2" fill="#1b6fd6"/><circle cx="6.5" cy="1.5" r="1.2" fill="#c7cfdb"/><circle cx="11.5" cy="1.5" r="1.2" fill="#c7cfdb"/></svg>
  <footer class="footer" style="top:595px">
    <div class="brand on-dark"><i class="mark"></i>Bramble Acres</div>
    <div class="f-col" style="left:78px;top:7px"><span class="f-head">Our Company</span><span>Lorem</span><span>Lorem</span><span>Lorem</span><span>Lorem</span></div>
    <div class="f-col" style="left:120px;top:7px"><span class="f-head">About</span><span>Support</span><span>Contact</span><span>Terms</span><span>Blog</span></div>
    <div class="f-col" style="left:158px;top:7px"><span class="f-head">Subscribe to our Newsletter</span></div>
    <div class="f-input" style="top:14px">Enter email address</div>
    <div class="f-btn" style="top:27px">Submit →</div>
    <span class="copy">Copyright © 2022</span>
    <div class="socials"><i></i><i></i><i></i><i></i></div>
  </footer>
</section>

<!-- ABOUT -->
<section class="page" style="left:252px;height:530px" aria-label="About page">
  <header class="nav">
    <div class="brand"><i class="mark"></i>Bramble Acres</div>
    <nav class="nav-links" style="left:82px"><span>Home</span><span class="current">About</span><span>Strategy</span><span>Projects</span></nav>
    <div class="btn">Investor Login</div>
  </header>
  <div class="photo" role="img" aria-label="Modern building against a blue sky" style="left:0;top:19px;width:225px;height:99px;background:linear-gradient(180deg,#3f78c9,#8eb4e0 55%,#d9dde2)"></div>
  <h1 class="hero-title" style="top:37px;font-size:15px">About<br>Bramble Acres</h1>
  <div style="left:0;top:118px;width:225px;height:130px;background:var(--light)"></div>
  <div class="card" style="left:15px;top:77px;width:132px;height:81px;border-radius:0">
    <h2 class="h-blue" style="left:10px;top:8px;font-size:7px;line-height:.95;font-weight:500">Lorem Ipsum Dolor Sit<br>Amet Consectetur.</h2>
    <p class="para" style="left:10px;top:28px;width:112px">Bramble Acres is a private real estate firm that focuses on the purchase, growth, oversight and sale of many kinds of commercial property, including multifamily, single-family, hospitality, self-storage and flex. The firm carries out its plan through long-standing ties that help it acquire and develop assets in select target markets. It is now centered on buying and building in the southern part of the country.</p>
  </div>
  <div style="left:149px;top:77px;width:60px;height:80px;background:linear-gradient(180deg,#1e7be6,#2a8cf0);color:#fff;text-align:center">
    <b style="left:0;top:9px;width:60px;font-size:8px;font-weight:500">2017</b><span style="left:0;top:18px;width:60px;font-size:3px">Year Established</span>
    <b style="left:0;top:31px;width:60px;font-size:8px;font-weight:500">80</b><span style="left:0;top:40px;width:60px;font-size:3px">Employees</span>
    <b style="left:0;top:53px;width:60px;font-size:8px;font-weight:500">$100M+</b><span style="left:0;top:62px;width:60px;font-size:3px;line-height:1">Assets Under Management</span>
  </div>
  <div class="photo" role="img" aria-label="Man walking on a wooded site" style="left:15px;top:170px;width:74px;height:70px;background:linear-gradient(180deg,#5e7a44,#7e6a40 60%,#a06a44)"></div>
  <h2 class="h-blue" style="left:96px;top:174px;font-size:7px;font-weight:500">Our Story</h2>
  <p class="para" style="left:96px;top:185px;width:113px">After years spent at several real estate development and private equity firms, Elias Marlow formed Bramble Acres in 2017 to pursue his long-held goal of building a firm that could acquire and develop Class A real estate across key metro markets with strong risk-adjusted returns. The core belief of the firm is built around a deep moral and ethical duty to manage the ties and assets of partners, clients and customers. That mindset has pushed the firm past $100 million in assets in five years.</p>
  <h2 class="h-blue" style="left:86px;top:258px;font-size:7px;font-weight:500">Meet The Team</h2>
  <svg style="left:147px;top:257px" width="44" height="8" viewBox="0 0 44 8"><g fill="none" stroke="#5d6676" stroke-width=".6"><rect x="1" y="1" width="6" height="6" rx="1.5"/><circle cx="15" cy="4" r="3"/><circle cx="26" cy="4" r="3"/><rect x="34" y="1.5" width="8" height="5"/><path d="M34 1.5l4 3 4-3"/></g></svg>
  <div class="member" style="left:15px;top:274px"><div class="img" role="img" aria-label="Portrait of the founder" style="background:linear-gradient(180deg,#6b7688,#3b4352)"></div><span class="name">Elias Marlow</span><span class="role">Founder &amp; CEO</span></div>
  <div class="member" style="left:81px;top:274px"><div class="img" role="img" aria-label="Portrait of a partner" style="background:linear-gradient(180deg,#eeeeee,#cfcfcf)"></div><span class="name">Dana Kerrow</span><span class="role">Partner</span></div>
  <div class="member" style="left:147px;top:274px"><div class="img" role="img" aria-label="Portrait of a partner" style="background:linear-gradient(180deg,#e9e9e9,#cbc4bb)"></div><span class="name">Lena Hartfield</span><span class="role">Partner</span></div>
  <div class="member" style="left:15px;top:357px"><div class="img" role="img" aria-label="Portrait of outside counsel" style="background:linear-gradient(180deg,#8ea0b5,#3e4756)"></div><span class="name">Owen Pratley</span><span class="role">Outside Counsel - Pell &amp; Greer</span></div>
  <div class="member" style="left:81px;top:357px;background:#1d3b66">
    <svg style="left:11px;top:36px" width="40" height="7" viewBox="0 0 40 7"><g fill="none" stroke="#fff" stroke-width=".6"><rect x="1" y="1" width="5" height="5" rx="1.3"/><circle cx="14" cy="3.5" r="2.5"/><circle cx="25" cy="3.5" r="2.5"/><rect x="32" y="1.3" width="7" height="4.4"/><path d="M32 1.3l3.5 2.5 3.5-2.5"/></g></svg>
  </div>
  <div class="member" style="left:147px;top:357px"><div class="img" role="img" aria-label="Portrait of the architect consultant" style="background:linear-gradient(180deg,#f2f2f2,#d6d6d6)"></div><span class="name">Julian Sato</span><span class="role">Architect Consultant</span></div>
  <div class="partners" style="top:449px;background:var(--blue)"><span class="lead" style="font-size:4.4px">Our Clients</span><span>Tavrin</span><span>Corveth</span><span>Lumo</span><span>Halden</span><span>Ashby &amp; Co</span></div>
  <footer class="footer" style="top:468px">
    <div class="brand on-dark"><i class="mark"></i>Bramble Acres</div>
    <div class="f-col" style="left:78px;top:7px"><span class="f-head">Our Company</span><span>Lorem</span><span>Lorem</span><span>Lorem</span><span>Lorem</span></div>
    <div class="f-col" style="left:120px;top:7px"><span class="f-head">About</span><span>Support</span><span>Contact</span><span>Terms</span><span>Blog</span></div>
    <div class="f-col" style="left:158px;top:7px"><span class="f-head">Subscribe to our Newsletter</span></div>
    <div class="f-input" style="top:14px">Enter email address</div>
    <div class="f-btn" style="top:27px">Submit →</div>
    <span class="copy">Copyright © 2022</span>
    <div class="socials"><i></i><i></i><i></i><i></i></div>
  </footer>
</section>

<!-- PROJECTS -->
<section class="page" style="left:488px;height:452px" aria-label="Projects page">
  <header class="nav">
    <div class="brand"><i class="mark"></i>Bramble Acres</div>
    <nav class="nav-links" style="left:82px"><span>Home</span><span>About</span><span>Strategy</span><span class="current">Projects</span></nav>
    <div class="btn">Investor Login</div>
  </header>
  <div class="photo" role="img" aria-label="Building facade at sunset" style="left:0;top:19px;width:225px;height:88px;background:linear-gradient(160deg,#1a1f2e,#3a3c48 55%,#b7874a)"></div>
  <h1 class="hero-title" style="top:46px;font-size:15px">Our Projects</h1>
  <p class="hero-copy" style="top:66px">This is the project page. It gives visitors a clear view of the context and history of each project. Edit this text to add any details you wish to share.</p>
  <div style="left:0;top:107px;width:225px;height:285px;background:var(--light)"></div>
  <div class="proj" style="left:15px;top:118px"><div class="img" role="img" aria-label="White industrial building" style="background:linear-gradient(180deg,#1d58b0,#dfe3e8)"></div><span class="tag">Ground-up Development</span><span class="name">Northline Industrial</span><span class="meta">Class A Industrial - 170,000 SF - 10.10 Acres</span></div>
  <div class="proj" style="left:114px;top:118px"><div class="img" role="img" aria-label="Red and blue apartment buildings" style="background:linear-gradient(180deg,#8fb1d4,#a6504a 50%,#4d6a3c)"></div><span class="tag">Value-Add Acquisition</span><span class="name">Vela at Parkline</span><span class="meta">Class A Multifamily - 244 Units - 4 Story - 230,428 SF - 4.89 Acres</span></div>
  <div class="proj" style="left:15px;top:208px"><div class="img" role="img" aria-label="Rendering of a residential complex" style="background:linear-gradient(180deg,#b8c8d6,#b6a27f 55%,#5f7246)"></div><span class="tag">Ground-up Development</span><span class="name">Stonebay Harbor Residences</span><span class="meta">Class A Multifamily - 176 Units - 4 Story - 159,280 SF - 3 Acres</span></div>
  <div class="proj" style="left:114px;top:208px"><div class="img" role="img" aria-label="Apartment entrance sign and landscaping" style="background:linear-gradient(180deg,#5b7ea6,#46523f 65%,#6c5a3c)"></div><span class="tag">Value-Add Acquisition</span><span class="name">Willow Run Apartments</span><span class="meta">Class C Multifamily - 212 Units - 2 Story - 136,936 SF - 11.24 Acres</span></div>
  <div class="proj" style="left:15px;top:297px"><div class="img" role="img" aria-label="Modern townhomes" style="background:linear-gradient(180deg,#2f6bc0,#9a9088 60%,#6f6a64)"></div><span class="tag">Ground-up Development</span><span class="name">Carden Homes</span><span class="meta">Class A Multifamily - 23 Units - 3 Story - 42,000 SF - .78 Acres</span></div>
  <div class="proj" style="left:114px;top:297px"><div class="img" role="img" aria-label="Aerial rendering of an apartment community" style="background:linear-gradient(180deg,#8fb2d6,#6f5a4c 50%,#5c7e4a)"></div><span class="tag">Ground-up Development</span><span class="name">Lakeshore at Fernbrook</span><span class="meta">Class A Multifamily - 373 Units - 3 Story - 345,297 SF - 24.31 Acres</span></div>
  <footer class="footer" style="top:390px">
    <div class="brand on-dark"><i class="mark"></i>Bramble Acres</div>
    <div class="f-col" style="left:78px;top:7px"><span class="f-head">Our Company</span><span>Lorem</span><span>Lorem</span><span>Lorem</span><span>Lorem</span></div>
    <div class="f-col" style="left:120px;top:7px"><span class="f-head">About</span><span>Support</span><span>Contact</span><span>Terms</span><span>Blog</span></div>
    <div class="f-col" style="left:158px;top:7px"><span class="f-head">Subscribe to our Newsletter</span></div>
    <div class="f-input" style="top:14px">Enter email address</div>
    <div class="f-btn" style="top:27px">Submit →</div>
    <span class="copy">Copyright © 2022</span>
    <div class="socials"><i></i><i></i><i></i><i></i></div>
  </footer>
</section>

<!-- STRATEGY -->
<section class="page" style="left:723px;height:430px" aria-label="Strategy page">
  <header class="nav">
    <div class="brand"><i class="mark"></i>Bramble Acres</div>
    <nav class="nav-links" style="left:82px"><span>Home</span><span>About</span><span class="current">Strategy</span><span>Projects</span></nav>
    <div class="btn">Investor Login</div>
  </header>
  <div class="photo" role="img" aria-label="Glass office tower seen from below" style="left:0;top:19px;width:225px;height:96px;background:linear-gradient(160deg,#233a5e,#4b6281 55%,#1b2a44)"></div>
  <h1 class="hero-title" style="top:42px;font-size:15px">Our Strategy</h1>
  <p class="hero-copy" style="top:62px">Lorem ipsum dolor sit amet consectetur. Ut venenatis elit turpis malesuada nunc mauris cursus. Semper nibh rhoncus lacus neque augue leo lacus.</p>
  <div style="left:0;top:115px;width:225px;height:265px;background:var(--light)"></div>
  <div class="stat" style="left:25px;top:94px;width:45px"><b>$100MM+</b><span>Assets Under<br>Management</span></div>
  <div class="stat" style="left:73px;top:94px;width:31px"><b>6</b><span>Current<br>Projects</span></div>
  <div class="stat" style="left:106px;top:94px;width:46px"><b style="font-size:5.4px">Marston, TX</b><span>Headquarters</span></div>
  <div class="stat" style="left:154px;top:94px;width:46px"><b>2017</b><span>Year<br>Established</span></div>
  <div class="photo" role="img" aria-label="Apartment clubhouse lounge interior" style="left:16px;top:132px;width:194px;height:68px;background:linear-gradient(100deg,#6b6158,#2f4f7e 45%,#9a6a5a 75%,#544a44)"></div>
  <div class="photo" role="img" aria-label="Blue glass buildings" style="left:0;top:224px;width:225px;height:76px;background:linear-gradient(120deg,#1c3f78,#355f9c 50%,#1a3466)"></div>
  <div class="card" style="left:47px;top:214px;width:131px;height:84px;border-radius:2px">
    <h3 class="focus-title" style="top:5px">Investment Focus</h3>
    <div class="focus-col" style="left:5px;top:16px;width:62px;height:64px"><b>Acquisitions: Distressed/Value-Add</b><ul><li>Value-Add Deals that offer a strong mix of yield and upside.</li><li>Distressed Assets with upside potential.</li><li>Major Metro Areas</li><li>Asset Value $10 - $75mm</li></ul></div>
    <div class="focus-col" style="left:70px;top:16px;width:56px;height:64px"><b>Development</b><ul><li>Site Selection</li><li>Undeveloped Land</li><li>Zoning and Entitlements</li><li>Urban Redevelopment</li><li>Multiple Build Types:</li><li>Single Story Garden</li><li>Wrap Construction</li><li>Podium Construction</li><li>Tiltwall</li></ul></div>
  </div>
  <div class="types" style="left:52px;top:285px;width:121px;height:22px"><b>Product<br>Types</b><ul><li>Multifamily</li><li>Industrial</li><li>SFR Communities</li></ul><ul><li>Self-Storage</li><li>Hospitality</li><li>Retail</li></ul></div>
  <div style="left:0;top:300px;width:225px;height:80px;background:var(--paper)"></div>
  <div class="photo" role="img" aria-label="Modern building at dusk" style="left:16px;top:318px;width:194px;height:52px;background:linear-gradient(120deg,#122a55,#2a4a80 50%,#14284e)"></div>
  <p style="left:60px;top:330px;width:106px;text-align:center;color:#fff;font-size:3px;line-height:1.35">Lorem ipsum dolor sit amet consectetur. Nunc elit magna pellentesque bibendum ut ac consectetur vitae. Facilisis justo sed et faucibus massa nam.</p>
  <div style="left:95px;top:348px;width:36px;height:11px;background:#fff;border-radius:2px;font-size:3.2px;display:flex;align-items:center;justify-content:center">Contact us</div>
  <footer class="footer" style="top:380px;height:50px">
    <div class="brand on-dark" style="top:20px"><i class="mark"></i>Bramble Acres</div>
    <div class="f-col" style="left:78px;top:7px"><span class="f-head">Our Company</span><span>Lorem</span><span>Lorem</span><span>Lorem</span><span>Lorem</span></div>
    <div class="f-col" style="left:120px;top:7px"><span class="f-head">About</span><span>Support</span><span>Contact</span><span>Terms</span><span>Blog</span></div>
    <div class="f-col" style="left:158px;top:7px"><span class="f-head">Subscribe to our Newsletter</span></div>
    <div class="f-input" style="top:14px">Enter email address</div>
    <div class="f-btn" style="top:27px">Submit →</div>
  </footer>
</section>

<!-- CONTACT -->
<section class="page" style="left:958px;height:352px" aria-label="Contact page">
  <header class="nav">
    <div class="brand"><i class="mark"></i>Bramble Acres</div>
    <nav class="nav-links" style="left:82px"><span>Home</span><span>About</span><span>Strategy</span><span>Projects</span></nav>
    <div class="btn">Investor Login</div>
  </header>
  <div class="photo" role="img" aria-label="Glass skyscrapers from below" style="left:0;top:19px;width:225px;height:58px;background:linear-gradient(120deg,#2e5590,#1a3462 50%,#3b6aa8)"></div>
  <h1 class="hero-title" style="top:35px;font-size:12px">Contact Us</h1>
  <p class="hero-copy" style="top:50px;padding:0 60px">Lorem ipsum dolor sit amet consectetur. Ut venenatis elit turpis malesuada nunc mauris cursus.</p>
  <span class="field-label" style="top:87px">First Name</span><div class="field" style="top:93px;height:11px"></div>
  <span class="field-label" style="top:108px">Last Name</span><div class="field" style="top:114px;height:11px"></div>
  <span class="field-label" style="top:129px">Email</span><div class="field" style="top:135px;height:11px"></div>
  <span class="field-label" style="top:150px">Subject</span><div class="field" style="top:156px;height:11px"></div>
  <span class="field-label" style="top:171px">Message</span><div class="field" style="top:178px;height:36px"></div>
  <div class="btn" style="left:15px;top:219px;width:77px;height:11px;font-size:3.6px">Submit</div>
  <div class="photo" role="img" aria-label="Street map of the office area" style="left:101px;top:90px;width:124px;height:140px;background:linear-gradient(135deg,#dfe8d8,#eef0ec 45%,#d6e2ef)"></div>
  <div style="left:0;top:243px;width:225px;height:47px;background:#d9e8f9"></div>
  <div class="info" style="left:15px;top:250px;width:62px"><h4>Employment</h4><p>To apply for a role with Bramble Acres, please send a cover letter along with your C.V. to: info@brambleacres.com</p></div>
  <div class="info" style="left:81px;top:250px;width:62px"><h4>Inquiries</h4><p>For any inquiries, questions or comments<br>Please call: (555) 014-2290<br>or fill out the following form</p></div>
  <div class="info" style="left:147px;top:250px;width:70px"><h4>Headquarters</h4><p>480 Harlow Ave. 7th Floor<br>Marston, TX 75000<br>info@brambleacres.com<br>Tel: (555) 014-2290</p></div>
  <footer class="footer" style="top:290px">
    <div class="brand on-dark"><i class="mark"></i>Bramble Acres</div>
    <div class="f-col" style="left:78px;top:7px"><span class="f-head">Our Company</span><span>Lorem</span><span>Lorem</span><span>Lorem</span><span>Lorem</span></div>
    <div class="f-col" style="left:120px;top:7px"><span class="f-head">About</span><span>Support</span><span>Contact</span><span>Terms</span><span>Blog</span></div>
    <div class="f-col" style="left:158px;top:7px"><span class="f-head">Subscribe to our Newsletter</span></div>
    <div class="f-input" style="top:14px">Enter email address</div>
    <div class="f-btn" style="top:27px">Submit →</div>
    <span class="copy">Copyright © 2022</span>
    <div class="socials"><i></i><i></i><i></i><i></i></div>
  </footer>
</section>

</body>
</html>
```